Web Infographic for Life Insurance

We need an infographic for our insurance site based on research commissioned previously. We have a report of statistics on the cost and coverage of life insurance in 1999 vs 2019. What we're looking for is an infographic that presents these statistics in an entertaining and informative way. Site is CoverWren.com
Target Market(s)
Americans ages 30-65 interested in life insurance.
Industry/Entity Type
Insurance
Number of Pages Required
1 page
Font styles to use
Sans Serif
Decorative
Colors
85cae6
faa54b
ffffff
86cfc6
Requirements
Must have
- Long vertical infographic readable on mobile devices
Nice to have
- Footnote references
Should not have
- Extremely small text
- Any brand logos or trademarked imagery other than for coverwren

```html
<!DOCTYPE html>
<html lang="en">
<head>
<meta charset="utf-8">
<title>Cost and Coverage of Life Insurance in 1999 vs 2019 – coverwren</title>
<link href="https://fonts.googleapis.com/css2?family=Poppins:wght@400;600;700&family=Roboto:wght@400;500;700&display=swap" rel="stylesheet">
<style>
:root{
  --sky:#7cc0e2;
  --sky-pale:#cdf0fb;
  --ring-pale:#d4eff7;
  --orange:#f7953d;
  --orange-light:#faa54b;
  --teal:#76c6bb;
  --teal-dark:#5fb3a8;
  --ink:#1d1d1f;
  --white:#ffffff;
  --stat-blue:#7cc3dc;
  --note-red:#d8262e;
  --note-green:#2f9a3a;
  --footer:#7cc0e2;
}
*{box-sizing:border-box;margin:0;padding:0}
html,body{width:1200px;height:3430px;overflow:hidden;background:var(--white)}
body{font-family:'Roboto',Arial,sans-serif;color:var(--ink)}
.page{position:relative;width:1200px;height:3430px;overflow:hidden}
.abs{position:absolute}
.heading{font-family:'Poppins',Arial,sans-serif;font-weight:700;text-align:center;line-height:1.18}

/* header */
.hero{position:absolute;left:0;top:0;width:1200px;height:522px;background:var(--sky)}
.brand{left:109px;top:34px;font-family:'Poppins',Arial,sans-serif;font-weight:600;font-size:23px;color:var(--white)}
.contact{left:862px;top:37px;font-size:19px;color:var(--white);display:flex;align-items:center;gap:10px}
.hero-title{left:0;top:88px;width:1200px;font-size:45px;color:var(--white)}
.era-art{width:220px;height:220px;border-radius:50%;top:195px;background:var(--white);display:flex;align-items:center;justify-content:center}
.era-art .fill{width:180px;height:150px;border-radius:18px}
.era-label{top:432px;width:220px;text-align:center;font-family:'Poppins',Arial,sans-serif;font-weight:700;font-size:23px;color:var(--white)}
.vs{left:553px;top:279px;width:100px;height:100px;background:var(--orange);transform:rotate(45deg)}
.vs-text{left:553px;top:305px;width:100px;text-align:center;font-family:'Poppins',Arial,sans-serif;font-weight:700;font-size:34px;color:var(--white)}

/* summary */
.summary-title{left:0;top:615px;width:1200px;font-size:33px}
.summary-title .range{color:var(--orange)}
.sum-item{top:716px;width:260px;text-align:center}
.sum-label{font-size:17.5px}
.sum-badge{margin:14px auto 0;width:94px;height:94px;border-radius:50% 50% 50% 50% / 42% 42% 58% 58%;background:var(--teal);display:flex;align-items:center;justify-content:center}
.sum-value{margin-top:12px;font-weight:700;font-size:18px}
.sum-arrow{top:781px}
.checks{left:495px;top:887px;font-size:16.5px;line-height:29px}
.checks li{list-style:none;display:flex;align-items:center;gap:10px}
.checks li:nth-child(2){margin-left:30px}

/* purchases */
.purchases{position:absolute;left:0;top:1050px;width:1200px;height:564px;background:var(--sky-pale)}
.purchases-title{left:0;top:1103px;width:1200px;font-size:33px}
.art{border-radius:14px}
.flow-arrow{top:1318px}
.note{font-size:14.5px;line-height:25px}
.note.red{left:466px;top:1462px;color:var(--note-red);width:290px}
.note.green{left:863px;top:1462px;color:var(--note-green);width:230px}

/* numbers columns */
.col{position:absolute;top:1614px;width:600px;height:748px}
.col.numbers{left:0;background:var(--teal)}
.col.cost{left:600px;background:var(--orange)}
.col-title{font-family:'Poppins',Arial,sans-serif;font-weight:700;font-size:32px;line-height:36px;color:var(--white);position:absolute;top:45px}
.stat{position:absolute;display:flex;align-items:center;gap:16px;color:var(--white)}
.stat-ring{position:relative;width:68px;height:68px;flex:none}
.stat-ring svg{position:absolute;left:0;top:0}
.stat-ring span{position:absolute;inset:0;display:flex;align-items:center;justify-content:center;font-family:'Poppins',Arial,sans-serif;font-weight:600;font-size:16px}
.stat p{font-size:15.5px;line-height:23px;width:370px}

/* reasons */
.reasons-title{left:0;top:2452px;width:1200px;font-size:33px}
.reason{width:260px;text-align:center}
.reason-ring{width:120px;height:120px;margin:0 auto;position:relative}
.reason-ring svg{position:absolute;left:0;top:0}
.reason-pct{margin-top:22px;font-family:'Poppins',Arial,sans-serif;font-weight:600;font-size:21px;color:var(--stat-blue)}
.reason-label{margin-top:4px;font-size:15.5px}

/* footer */
.footer{position:absolute;left:0;top:3350px;width:1200px;height:80px;background:var(--footer);color:#2d4b5a;font-size:14.5px;display:flex;align-items:center;justify-content:center}
</style>
</head>
<body>
<main class="page">

  <header class="hero">
    <div class="abs brand">coverwren</div>
    <div class="abs contact">
      <svg width="20" height="15" viewBox="0 0 20 15"><rect x="0" y="0" width="20" height="15" rx="2" fill="#fff"/><path d="M1 1.5l9 7 9-7" stroke="#7cc0e2" stroke-width="2" fill="none"/></svg>
      info@coverwren.com
    </div>
    <h1 class="abs heading hero-title">Cost and Coverage of Life Insurance<br>in 1999 vs 2019</h1>

    <div class="abs era-art" style="left:199px">
      <div class="fill" role="img" aria-label="Illustration of a family standing beside an insurance document" style="background:linear-gradient(135deg,#cfe3f7,#f3a7b5)"></div>
    </div>
    <div class="abs era-label" style="left:199px">1999</div>

    <div class="abs vs"></div>
    <div class="abs vs-text">VS</div>

    <div class="abs era-art" style="left:782px">
      <div class="fill" role="img" aria-label="Illustration of people under a large green umbrella with documents and a shield" style="background:linear-gradient(135deg,#bfe9d6,#3fae8f)"></div>
    </div>
    <div class="abs era-label" style="left:782px">2019</div>
  </header>

  <section>
    <h2 class="abs heading summary-title">Summary Statistics <span class="range">(1992–1997)</span></h2>

    <div class="abs sum-item" style="left:60px">
      <div class="sum-label">Type Term Premium</div>
      <div class="sum-badge">
        <svg width="48" height="40" viewBox="0 0 48 40" fill="none" stroke="#1d1d1f" stroke-width="2.2" stroke-linejoin="round"><path d="M10 2h28l8 11-22 25L2 13z"/><path d="M2 13h44M17 2l-3 11 10 25 10-25-3-11M24 2l-10 11M24 2l10 11"/></svg>
      </div>
      <div class="sum-value">3.62</div>
    </div>
    <svg class="abs sum-arrow" style="left:357px" width="40" height="28" viewBox="0 0 40 28"><path d="M1 14h36M25 3l12 11-12 11" stroke="#1d1d1f" stroke-width="2" fill="none"/></svg>

    <div class="abs sum-item" style="left:425px">
      <div class="sum-label">Length of policy</div>
      <div class="sum-badge">
        <svg width="44" height="44" viewBox="0 0 44 44" fill="none" stroke="#1d1d1f" stroke-width="2"><rect x="6" y="6" width="26" height="34" rx="2"/><rect x="14" y="2" width="10" height="7" rx="1"/><path d="M11 17h6M11 24h6M11 31h6M21 17h6"/><rect x="22" y="24" width="18" height="15"/><path d="M22 29h18M31 24v15"/></svg>
      </div>
      <div class="sum-value">3.62</div>
    </div>
    <svg class="abs sum-arrow" style="left:712px" width="40" height="28" viewBox="0 0 40 28"><path d="M1 14h36M25 3l12 11-12 11" stroke="#1d1d1f" stroke-width="2" fill="none"/></svg>

    <div class="abs sum-item" style="left:832px">
      <div class="sum-label">Real Amount of Policy</div>
      <div class="sum-badge">
        <svg width="46" height="44" viewBox="0 0 46 44" fill="none" stroke="#1d1d1f" stroke-width="2" stroke-linejoin="round"><rect x="18" y="4" width="24" height="16" rx="2"/><rect x="22" y="10" width="24" height="16" rx="2"/><path d="M2 30l8-6h10l6 3h-8M2 40l6-3h14l14-9"/></svg>
      </div>
      <div class="sum-value">3.62</div>
    </div>

    <ul class="abs checks">
      <li><svg width="14" height="14" viewBox="0 0 14 14"><circle cx="7" cy="7" r="7" fill="#f7953d"/><path d="M3.8 7.2l2.2 2.2 4.2-4.4" stroke="#fff" stroke-width="1.8" fill="none"/></svg>Non-Smoker</li>
      <li><svg width="14" height="14" viewBox="0 0 14 14"><circle cx="7" cy="7" r="7" fill="#f7953d"/><path d="M3.8 7.2l2.2 2.2 4.2-4.4" stroke="#fff" stroke-width="1.8" fill="none"/></svg>Male</li>
    </ul>
  </section>

  <section class="purchases"></section>
  <h2 class="abs heading purchases-title">Number of life insurance policy purchases in<br>the United States from 1998 to 2018</h2>
  <div class="abs art" role="img" aria-label="Illustration of a group of business people in suits holding briefcases" style="left:110px;top:1262px;width:195px;height:140px;background:linear-gradient(180deg,#a9c6ef,#253a7a)"></div>
  <svg class="abs flow-arrow" style="left:362px" width="78" height="30" viewBox="0 0 78 30"><path d="M1 15h74M61 3l14 12-14 12" stroke="#1d1d1f" stroke-width="2" fill="none"/></svg>
  <div class="abs art" role="img" aria-label="Dotted map of the United States" style="left:486px;top:1265px;width:254px;height:180px;background:linear-gradient(135deg,#6f8fc9,#3f5fa8)"></div>
  <svg class="abs flow-arrow" style="left:757px" width="78" height="30" viewBox="0 0 78 30"><path d="M1 15h74M61 3l14 12-14 12" stroke="#1d1d1f" stroke-width="2" fill="none"/></svg>
  <div class="abs art" role="img" aria-label="Illustration of a money bag with coins and a rising growth chart" style="left:892px;top:1279px;width:167px;height:140px;background:linear-gradient(135deg,#9fd8e8,#f3b23a)"></div>
  <p class="abs note red">Note: Growth of the Internet has reduced term life prices by 8–15 percent.</p>
  <p class="abs note green">Approximately 27.8 million life insurance policies were purchased in the United States.</p>

  <section class="col numbers">
    <h2 class="col-title" style="left:93px">Life insurance by the<br>numbers</h2>

    <div class="stat" style="left:90px;top:145px">
      <div class="stat-ring"><svg width="68" height="68" viewBox="0 0 68 68"><circle cx="34" cy="34" r="30" fill="none" stroke="#fff" stroke-width="5"/><circle cx="34" cy="34" r="30" fill="none" stroke="#f7953d" stroke-width="5" pathLength="100" stroke-dasharray="57 100" transform="rotate(-90 34 34)"/></svg><span>57%</span></div>
      <p>57% &nbsp;Percent of American adults who have life insurance‡</p>
    </div>
    <div class="stat" style="left:90px;top:261px">
      <div class="stat-ring"><svg width="68" height="68" viewBox="0 0 68 68"><circle cx="34" cy="34" r="30" fill="none" stroke="#fff" stroke-width="5"/><circle cx="34" cy="34" r="30" fill="none" stroke="#f7953d" stroke-width="5" pathLength="100" stroke-dasharray="32 100" transform="rotate(-90 34 34)"/></svg><span>32%</span></div>
      <p>32% Of American adults with life insurance, the percent who only have group coverage — which usually isn’t enough (and is rarely portable)‡</p>
    </div>
    <div class="stat" style="left:90px;top:383px">
      <div class="stat-ring"><svg width="68" height="68" viewBox="0 0 68 68"><circle cx="34" cy="34" r="30" fill="none" stroke="#fff" stroke-width="5"/><circle cx="34" cy="34" r="30" fill="none" stroke="#f7953d" stroke-width="5" pathLength="100" stroke-dasharray="57 100" transform="rotate(-90 34 34)"/></svg><span>57%</span></div>
      <p>10x to 12x &nbsp;The multiples of your annual income that most financial advisors recommend you need when buying life insurance for income replacement†</p>
    </div>
    <div class="stat" style="left:90px;top:500px">
      <div class="stat-ring"><svg width="68" height="68" viewBox="0 0 68 68"><circle cx="34" cy="34" r="30" fill="none" stroke="#fff" stroke-width="5"/><circle cx="34" cy="34" r="30" fill="none" stroke="#f7953d" stroke-width="5" pathLength="100" stroke-dasharray="50 100" transform="rotate(-90 34 34)"/></svg><span>50%</span></div>
      <p>50% Percent of life insurance policies are purchased via independent agents</p>
    </div>
    <div class="stat" style="left:90px;top:616px">
      <div class="stat-ring"><svg width="68" height="68" viewBox="0 0 68 68"><circle cx="34" cy="34" r="30" fill="none" stroke="#fff" stroke-width="5"/><circle cx="34" cy="34" r="30" fill="none" stroke="#f7953d" stroke-width="5" pathLength="100" stroke-dasharray="40 100" transform="rotate(-90 34 34)"/></svg><span>40%</span></div>
      <p>40% Percent of life insurance policies purchased via affiliated agents (meaning they only sell products for one insurance company)‡</p>
    </div>
  </section>

  <section class="col cost">
    <h2 class="col-title" style="left:66px">Stats about the cost of life<br>insurance</h2>

    <div class="stat" style="left:63px;top:145px">
      <div class="stat-ring"><svg width="68" height="68" viewBox="0 0 68 68"><circle cx="34" cy="34" r="30" fill="none" stroke="#fff" stroke-width="5"/><circle cx="34" cy="34" r="30" fill="none" stroke="#76c6bb" stroke-width="5" pathLength="100" stroke-dasharray="8 100" transform="rotate(-90 34 34)"/></svg><span>8%</span></div>
      <p>6x-10x How much more permanent life insurance (like whole life insurance) costs vs. term life insurance†</p>
    </div>
    <div class="stat" style="left:63px;top:235px">
      <div class="stat-ring"><svg width="68" height="68" viewBox="0 0 68 68"><circle cx="34" cy="34" r="30" fill="none" stroke="#fff" stroke-width="5"/><circle cx="34" cy="34" r="30" fill="none" stroke="#76c6bb" stroke-width="5" pathLength="100" stroke-dasharray="8 100" transform="rotate(-90 34 34)"/></svg><span>8%</span></div>
      <p>8% * Average percent increase in your insurance costs as you age, assuming your health stays the same†</p>
    </div>
    <div class="stat" style="left:63px;top:331px">
      <div class="stat-ring"><svg width="68" height="68" viewBox="0 0 68 68"><circle cx="34" cy="34" r="30" fill="none" stroke="#fff" stroke-width="5"/><circle cx="34" cy="34" r="30" fill="none" stroke="#76c6bb" stroke-width="5" pathLength="100" stroke-dasharray="57 100" transform="rotate(-90 34 34)"/></svg><span>57%</span></div>
      <p>30% The average cost difference between sequential health ratings (preferred vs standard, for example)†</p>
    </div>
    <div class="stat" style="left:63px;top:433px">
      <div class="stat-ring"><svg width="68" height="68" viewBox="0 0 68 68"><circle cx="34" cy="34" r="30" fill="none" stroke="#fff" stroke-width="5"/><circle cx="34" cy="34" r="30" fill="none" stroke="#76c6bb" stroke-width="5" pathLength="100" stroke-dasharray="25 100" transform="rotate(-90 34 34)"/></svg><span>2.5%</span></div>
      <p>2x to 3x How much rates for smokers cost vs. rates for nonsmokers (but a year after you quit smoking, most companies will offer you nonsmoker rates)†</p>
    </div>
    <div class="stat" style="left:63px;top:531px">
      <div class="stat-ring"><svg width="68" height="68" viewBox="0 0 68 68"><circle cx="34" cy="34" r="30" fill="none" stroke="#fff" stroke-width="5"/><circle cx="34" cy="34" r="30" fill="none" stroke="#76c6bb" stroke-width="5" pathLength="100" stroke-dasharray="50 100" transform="rotate(-90 34 34)"/></svg><span>50%</span></div>
      <p>50% The average difference between the least expensive and most expensive rate for the same person across insurance companies†</p>
    </div>
    <div class="stat" style="left:63px;top:628px">
      <div class="stat-ring"><svg width="68" height="68" viewBox="0 0 68 68"><circle cx="34" cy="34" r="30" fill="none" stroke="#fff" stroke-width="5"/><circle cx="34" cy="34" r="30" fill="none" stroke="#76c6bb" stroke-width="5" pathLength="100" stroke-dasharray="40 100" transform="rotate(-90 34 34)"/></svg><span>40%</span></div>
      <p>30% Percent difference between premiums for men and women (with women paying nearly ⅓ less than men, on average)†</p>
    </div>
  </section>

  <section>
    <h2 class="abs heading reasons-title">Top reasons for buying life<br>insurance in the U.S.</h2>

    <!-- row 1 -->
    <div class="abs reason" style="left:59px;top:2577px">
      <div class="reason-ring"><svg width="120" height="120" viewBox="0 0 120 120"><circle cx="60" cy="60" r="56" fill="none" stroke="#d4eff7" stroke-width="5"/><circle cx="60" cy="60" r="56" fill="none" stroke="#f7953d" stroke-width="5" pathLength="100" stroke-dasharray="30 100" transform="rotate(-90 60 60)"/><g fill="none" stroke="#7cc3dc" stroke-width="2"><circle cx="62" cy="46" r="10"/><path d="M62 40v12M38 72l10-6h14l4 4h-10M38 80l10-4h18l16-12"/></g></svg></div>
      <div class="reason-pct">37%</div><div class="reason-label">Income replacement</div>
    </div>
    <div class="abs reason" style="left:335px;top:2577px">
      <div class="reason-ring"><svg width="120" height="120" viewBox="0 0 120 120"><circle cx="60" cy="60" r="56" fill="none" stroke="#d4eff7" stroke-width="5"/><circle cx="60" cy="60" r="56" fill="none" stroke="#f7953d" stroke-width="5" pathLength="100" stroke-dasharray="30 100" transform="rotate(-90 60 60)"/><g fill="none" stroke="#7cc3dc" stroke-width="2"><path d="M40 58l5-14h30l5 14"/><rect x="36" y="58" width="48" height="16" rx="3"/><path d="M42 74v6h8v-6M70 74v6h8v-6"/><circle cx="45" cy="66" r="2.5"/><circle cx="75" cy="66" r="2.5"/></g></svg></div>
      <div class="reason-pct">30%</div><div class="reason-label">Burial/final expenses</div>
    </div>
    <div class="abs reason" style="left:611px;top:2577px">
      <div class="reason-ring"><svg width="120" height="120" viewBox="0 0 120 120"><circle cx="60" cy="60" r="56" fill="none" stroke="#d4eff7" stroke-width="5"/><circle cx="60" cy="60" r="56" fill="none" stroke="#f7953d" stroke-width="5" pathLength="100" stroke-dasharray="28 100" transform="rotate(-90 60 60)"/><g fill="none" stroke="#7cc3dc" stroke-width="2"><rect x="62" y="36" width="20" height="26" rx="2"/><path d="M62 45h20M62 53h20"/><rect x="38" y="58" width="20" height="26" rx="2"/><path d="M38 67h20M38 75h20M48 50l10-10M58 40v6M58 40h-6M64 78l8-8"/></g></svg></div>
      <div class="reason-pct">28%</div><div class="reason-label">Wealth transfer</div>
    </div>
    <div class="abs reason" style="left:886px;top:2577px">
      <div class="reason-ring"><svg width="120" height="120" viewBox="0 0 120 120"><circle cx="60" cy="60" r="56" fill="none" stroke="#d4eff7" stroke-width="5"/><circle cx="60" cy="60" r="56" fill="none" stroke="#f7953d" stroke-width="5" pathLength="100" stroke-dasharray="27 100" transform="rotate(-90 60 60)"/><g fill="none" stroke="#7cc3dc" stroke-width="2"><path d="M44 36h24l10 10v38H44z"/><path d="M50 52l9-7 9 7v9H50zM50 68h22M50 74h22"/></g></svg></div>
      <div class="reason-pct">27%</div><div class="reason-label">Pay off mortgage</div>
    </div>

    <!-- row 2 -->
    <div class="abs reason" style="left:59px;top:2817px">
      <div class="reason-ring"><svg width="120" height="120" viewBox="0 0 120 120"><circle cx="60" cy="60" r="56" fill="none" stroke="#d4eff7" stroke-width="5"/><circle cx="60" cy="60" r="56" fill="none" stroke="#f7953d" stroke-width="5" pathLength="100" stroke-dasharray="19 100" transform="rotate(-90 60 60)"/><g fill="none" stroke="#7cc3dc" stroke-width="2"><rect x="40" y="38" width="40" height="44" rx="3"/><path d="M48 54a12 8 0 0 1 24 0zM60 54v8M48 68h24M48 74h24"/></g></svg></div>
      <div class="reason-pct">19%</div><div class="reason-label">Replaced a policy</div>
    </div>
    <div class="abs reason" style="left:335px;top:2817px">
      <div class="reason-ring"><svg width="120" height="120" viewBox="0 0 120 120"><circle cx="60" cy="60" r="56" fill="none" stroke="#d4eff7" stroke-width="5"/><circle cx="60" cy="60" r="56" fill="none" stroke="#f7953d" stroke-width="5" pathLength="100" stroke-dasharray="17 100" transform="rotate(-90 60 60)"/><g fill="none" stroke="#7cc3dc" stroke-width="2"><path d="M44 36h20v46H44z"/><circle cx="54" cy="48" r="4"/><path d="M54 52v10"/><ellipse cx="72" cy="60" rx="8" ry="3"/><path d="M64 60v18c0 2 16 2 16 0V60M64 66c0 2 16 2 16 0M64 72c0 2 16 2 16 0"/></g></svg></div>
      <div class="reason-pct">17%</div><div class="reason-label">Tax advantaged save/invest</div>
    </div>
    <div class="abs reason" style="left:611px;top:2817px">
      <div class="reason-ring"><svg width="120" height="120" viewBox="0 0 120 120"><circle cx="60" cy="60" r="56" fill="none" stroke="#d4eff7" stroke-width="5"/><circle cx="60" cy="60" r="56" fill="none" stroke="#f7953d" stroke-width="5" pathLength="100" stroke-dasharray="14 100" transform="rotate(-90 60 60)"/><g fill="none" stroke="#7cc3dc" stroke-width="2"><path d="M40 82V50h14v32M54 82V40h14v42M68 82V54h14v28M36 82h50M45 58h4M45 66h4M59 48h4M59 56h4M59 64h4M73 62h4M73 70h4"/></g></svg></div>
      <div class="reason-pct">14%</div><div class="reason-label">Estate taxes/liquidity</div>
    </div>
    <div class="abs reason" style="left:886px;top:2817px">
      <div class="reason-ring"><svg width="120" height="120" viewBox="0 0 120 120"><circle cx="60" cy="60" r="56" fill="none" stroke="#d4eff7" stroke-width="5"/><circle cx="60" cy="60" r="56" fill="none" stroke="#f7953d" stroke-width="5" pathLength="100" stroke-dasharray="14 100" transform="rotate(-90 60 60)"/><g fill="none" stroke="#7cc3dc" stroke-width="2"><path d="M40 48l24-10 24 10-24 10zM50 52v10c8 6 20 6 28 0V52M86 49v14"/><circle cx="50" cy="72" r="10"/><path d="M50 66v12"/></g></svg></div>
      <div class="reason-pct">14%</div><div class="reason-label">Funds for college education</div>
    </div>

    <!-- row 3 -->
    <div class="abs reason" style="left:192px;top:3058px">
      <div class="reason-ring"><svg width="120" height="120" viewBox="0 0 120 120"><circle cx="60" cy="60" r="56" fill="none" stroke="#d4eff7" stroke-width="5"/><circle cx="60" cy="60" r="56" fill="none" stroke="#f7953d" stroke-width="5" pathLength="100" stroke-dasharray="13 100" transform="rotate(-90 60 60)"/><g fill="none" stroke="#7cc3dc" stroke-width="2"><rect x="38" y="48" width="44" height="10"/><rect x="42" y="58" width="36" height="24"/><path d="M60 48v34M60 48c-6-10-16-8-12 0M60 48c6-10 16-8 12 0"/></g></svg></div>
      <div class="reason-pct">13%</div><div class="reason-label">Charitable gift</div>
    </div>
    <div class="abs reason" style="left:469px;top:3058px">
      <div class="reason-ring"><svg width="120" height="120" viewBox="0 0 120 120"><circle cx="60" cy="60" r="56" fill="none" stroke="#d4eff7" stroke-width="5"/><circle cx="60" cy="60" r="56" fill="none" stroke="#f7953d" stroke-width="5" pathLength="100" stroke-dasharray="8 100" transform="rotate(-90 60 60)"/><g fill="none" stroke="#7cc3dc" stroke-width="2"><circle cx="60" cy="50" r="8"/><circle cx="42" cy="56" r="6"/><circle cx="78" cy="56" r="6"/><path d="M44 76c0-10 32-10 32 0zM32 76c0-8 10-10 14-8M88 76c0-8-10-10-14-8"/></g></svg></div>
      <div class="reason-pct">8%</div><div class="reason-label">Supplement group coverage</div>
    </div>
    <div class="abs reason" style="left:745px;top:3058px">
      <div class="reason-ring"><svg width="120" height="120" viewBox="0 0 120 120"><circle cx="60" cy="60" r="56" fill="none" stroke="#d4eff7" stroke-width="5"/><circle cx="60" cy="60" r="56" fill="none" stroke="#f7953d" stroke-width="5" pathLength="100" stroke-dasharray="8 100" transform="rotate(-90 60 60)"/><g fill="none" stroke="#7cc3dc" stroke-width="2"><circle cx="60" cy="42" r="9"/><path d="M60 37v10M34 62l10-8 10 4 10-4 10 4 12 4M40 60l12 14 6-2 8 6 14-14"/></g></svg></div>
      <div class="reason-pct">8%</div><div class="reason-label">Business purposes</div>
    </div>
  </section>

  <footer class="footer">© 2020 coverwren. All Rights Reserved</footer>
</main>
</body>
</html>
```